Printing company needs stellar web site!

We need a website for a printing company based in Atlanta, Georgia, USA. Our company is 26 years old and just this year did a logo and branding refresh. Now we need our website to be refreshed as well.

Please see the attached source files for our new logo and stationary design.

Printing

```html
<!DOCTYPE html>
<html lang="en">
<head>
<meta charset="utf-8">
<title>Printwell – Printing &amp; Labels</title>
<link href="https://fonts.googleapis.com/css2?family=Roboto:wght@400;500;700;900&family=Noticia+Text&family=Open+Sans:wght@400;600;700&display=swap" rel="stylesheet">
<style>
:root{
  --brand:#0d4f95;
  --brand-dark:#0b3f78;
  --footer:#174e86;
  --footer-bar:#1d6db5;
  --panel:#f8f4ea;
  --ink:#444;
  --muted:#666;
  --gold:#c9a94c;
}
*{margin:0;padding:0;box-sizing:border-box}
html,body{width:867px;height:1200px;overflow:hidden}
body{position:relative;background:linear-gradient(#fff 0,#f1f1f1 80px,#d6d6d6 960px);font-family:"Open Sans",sans-serif;color:var(--ink)}
.abs{position:absolute}
.logo{left:100px;top:10px}
.logo .mark{left:0;top:2px;width:36px;height:36px;border-radius:50%;border:5px solid var(--brand)}
.logo .name{left:42px;top:-2px;font:900 34px/40px "Roboto",sans-serif;color:var(--brand);letter-spacing:1px}
.logo .tag{left:42px;top:36px;font:600 6.4px "Open Sans",sans-serif;color:var(--brand);white-space:nowrap}
.slogan{left:388px;top:15px;width:250px;text-align:center;font:14.5px/20px "Noticia Text",serif;color:#555;white-space:nowrap}
.call{left:668px;top:20px;font:500 13px/16px "Roboto",sans-serif;color:var(--brand)}
.call b{font-weight:700;font-size:14px}
.nav{left:94px;top:72px;width:679px;height:21px;background:linear-gradient(#2577c4,var(--brand-dark));border-radius:8px 8px 2px 2px;display:flex;padding:0 6px}
.nav span{flex:auto;text-align:center;color:#fff;font:400 11px/21px "Roboto",sans-serif;border-right:1px solid #0a3a6c}
.nav span:last-child{border:0}
.badge{left:108px;top:106px;width:154px;height:71px;background:linear-gradient(135deg,#e8d08a,var(--gold));border:2px solid #b89433;border-radius:3px}
.badge i{position:absolute;left:10px;top:6px;width:100px;height:55px;background:#a8193e}
.badge-cap{left:108px;top:180px;width:154px;text-align:center;font:12px "Noticia Text",serif;color:#a8193e}
.panel{background:var(--panel);border-radius:3px;box-shadow:0 6px 6px -4px rgba(0,0,0,.35)}
.tab{height:20px;padding:0 22px 0 9px;background:linear-gradient(#1d68b3,var(--brand-dark));color:#fff;font:700 15px/20px "Roboto",sans-serif;clip-path:polygon(0 0,88% 0,100% 100%,0 100%);border-bottom:2px solid #7ea6d1;white-space:nowrap}
.cats{left:110px;top:210px;width:152px;height:408px}
.cats ul{list-style:none;position:absolute;left:8px;top:42px;width:136px}
.cats li{font:8.5px/28.3px "Open Sans",sans-serif;color:#444;border-bottom:1px solid #e6dfcf;white-space:nowrap}
.cats li:last-child{border:0}
.news{left:110px;top:638px;width:152px;height:192px}
.date{width:28px;height:30px;text-align:center;background:#ddd;font:700 8px/12px "Roboto",sans-serif;color:#333}
.date em{display:block;font-style:normal;background:#999;color:#fff}
.date b{font-size:12px;line-height:18px}
.news p{font:9px/14px "Open Sans",sans-serif;color:#555}
.link{font:700 10.5px "Roboto",sans-serif;color:var(--brand);white-space:nowrap}
.news-sep{left:9px;top:96px;width:134px;border-top:1px dashed #ccc}
.letter{left:110px;top:850px;width:152px;height:90px}
.letter .in{left:6px;top:58px;width:90px;height:18px;background:#fff;border:1px solid #bbb;font:9px/16px "Open Sans",sans-serif;color:#777;padding-left:3px;white-space:nowrap;overflow:hidden}
.letter .btn{left:100px;top:58px;width:47px;height:18px;background:var(--brand-dark);color:#fff;font:9.5px/18px "Open Sans",sans-serif;text-align:center}
.slider{left:279px;top:110px;width:472px;height:202px;background:linear-gradient(120deg,#6b3fa0,#2f7bd0 20%,#2eb38b 38%,#e8d23a 55%,#f08a2a 70%,#d62e3a 85%,#8a1d4a);box-shadow:0 8px 8px -5px rgba(0,0,0,.4)}
.slider .cap{left:0;bottom:0;width:100%;height:26px;background:rgba(236,236,236,.93);font:12px/26px "Noticia Text",serif;color:#222;text-align:center;white-space:nowrap}
.arrow{width:26px;height:34px;background:#eee;top:76px;border-radius:50%}
.feat{left:273px;top:334px;width:485px;height:357px}
.thumb{width:135px;height:101px;border:1px solid #999}
.pcap{width:135px;font:600 9.5px/12px "Open Sans",sans-serif;color:#555}
.serv{left:276px;top:714px;width:482px;height:116px}
.svc{width:140px;height:70px;top:39px}
.svc span{position:absolute;bottom:2px;width:100%;text-align:center;color:#fff;font:700 9.5px "Roboto",sans-serif;white-space:nowrap}
.clients{left:276px;top:850px;width:482px;height:90px}
.cl{top:55px;font:600 15px/28px "Open Sans",sans-serif;color:#777}
.circ{width:15px;height:15px;border-radius:50%;background:#999;top:61px}
footer{left:0;top:968px;width:867px;height:232px;background:var(--footer);color:#fff}
footer h4{font:700 11px "Roboto",sans-serif}
footer p{font:8.8px/13.4px "Open Sans",sans-serif}
.bar{left:0;top:164px;width:867px;height:36px;background:var(--footer-bar)}
.bar span{font:400 9.5px/36px "Roboto",sans-serif;margin-right:14px}
.quote{left:355px;top:48px;width:179px;height:70px;background:#1f6fbd;border-radius:8px;font:8.8px/13.4px "Open Sans",sans-serif;padding:5px 10px}
.soc{width:19px;height:19px;border-radius:50%;background:#2a78c3;top:203px}
</style>
</head>
<body>
<header>
  <div class="abs logo"><div class="abs mark"></div><div class="abs name">PRINTWELL</div><div class="abs tag">OUTSTANDING SERVICE • QUALITY PRODUCT • COMPETITIVE PRICING.</div></div>
  <div class="abs slogan">We Know, we understand<br>we will exceed your expectations.</div>
  <div class="abs call">
    <svg width="12" height="22" style="position:absolute;left:-16px;top:6px" viewBox="0 0 12 22"><path d="M9 1C2 3 1 19 9 21l2-4c-4-1-4-11 0-12z" fill="#222"/></svg>
    call us<br><b>800.555.0142</b></div>
  <nav class="abs nav"><span>Home</span><span>Markets</span><span>Products</span><span>Services</span><span>About Us</span><span>Contact Us</span><span>Customer Service</span><span>FTP</span></nav>
</header>

<div class="abs badge" role="img" aria-label="Trade guild fifty-year anniversary badge"><i></i></div>
<div class="abs badge-cap">Guild's Golden Anniversary</div>

<aside class="abs panel cats">
  <div class="abs tab" style="left:-4px;top:8px;width:147px">Categories</div>
  <ul>
    <li>• 4 Color Process</li><li>• Color Matching</li><li>• Flexible Packaging</li><li>• Piggyback</li><li>• Two Side Print</li><li>• UV Printing</li><li>• UV Varnish</li><li>• Gloss and Matte Laminate</li><li>• Labels</li><li>• Spacility Label Constructions</li><li>• Label Substrates</li><li>• Tooling Types</li>
  </ul>
</aside>

<aside class="abs panel news">
  <div class="abs tab" style="left:-3px;top:8px;width:146px">Latest News</div>
  <div class="abs date" style="left:7px;top:40px"><em>July</em><b>12</b></div>
  <p class="abs" style="left:46px;top:40px;width:100px">Lorem ipsju lorjaer lor ljraoieuroiasure lore</p>
  <p class="abs" style="left:9px;top:74px">Lorem ipsju lorjaer loremi iek</p>
  <div class="abs news-sep"></div>
  <div class="abs date" style="left:7px;top:109px"><em>July</em><b>12</b></div>
  <p class="abs" style="left:46px;top:109px;width:100px">Lorem ipsju lorjaer lor ljraoieuroiasure lore</p>
  <p class="abs" style="left:9px;top:143px">Lorem ipsju lorjaer loremi iek</p>
  <div class="abs link" style="left:74px;top:171px">View More +</div>
</aside>

<aside class="abs panel letter">
  <div class="abs tab" style="left:-3px;top:8px;width:146px">Newsletter</div>
  <p class="abs" style="left:8px;top:38px;font-size:9.5px;color:#555">Get the latest updates</p>
  <div class="abs in">Enter your email ID</div>
  <div class="abs btn">Subscribe</div>
</aside>

<section class="abs slider" role="img" aria-label="Fanned colour swatch guide in a full spectrum">
  <div class="abs arrow" style="left:-8px"><svg width="26" height="34"><path d="M16 10l-7 7 7 7" stroke="#222" stroke-width="4" fill="none"/></svg></div>
  <div class="abs arrow" style="right:-8px"><svg width="26" height="34"><path d="M10 10l7 7-7 7" stroke="#222" stroke-width="4" fill="none"/></svg></div>
  <div class="abs cap">We Provide Outstanding Service, Quality Product &amp; Competitive Pricing.</div>
</section>

<section class="abs panel feat">
  <div class="abs tab" style="left:-6px;top:8px;width:159px">Featured Products</div>
  <div class="abs thumb" style="left:13px;top:43px;background:linear-gradient(135deg,#cfe6e0,#eef2f2 60%,#f07a3a)" role="img" aria-label="Printed business stationery set"></div>
  <div class="abs thumb" style="left:174px;top:43px;background:linear-gradient(120deg,#c0304a,#e8b53a,#3aa56a,#3068c0,#7a3fa0)" role="img" aria-label="Colour swatch fan"></div>
  <div class="abs thumb" style="left:336px;top:43px;background:linear-gradient(90deg,#e8e8e8 55%,#5aa83a)" role="img" aria-label="Stack of printed brochures"></div>
  <div class="abs pcap" style="left:16px;top:156px">Duis aute irure dolor minim veniam</div>
  <div class="abs pcap" style="left:177px;top:156px">Duis aute irure dolor minim veniam</div>
  <div class="abs pcap" style="left:339px;top:156px">Duis aute irure dolor minim veniam</div>
  <div class="abs thumb" style="left:13px;top:192px;background:linear-gradient(#555,#6a3a8a 30%,#2a8ac0 70%,#333)" role="img" aria-label="Large format printer producing a poster"></div>
  <div class="abs thumb" style="left:174px;top:192px;background:linear-gradient(150deg,#f0c020,#e83a8a,#3a60c0,#2ab09a)" role="img" aria-label="Colour swatch fan"></div>
  <div class="abs thumb" style="left:336px;top:192px;background:linear-gradient(90deg,#e8e8e8 55%,#5aa83a)" role="img" aria-label="Stack of printed brochures"></div>
  <div class="abs pcap" style="left:16px;top:304px">Duis aute irure dolor minim veniam</div>
  <div class="abs pcap" style="left:177px;top:304px">Duis aute irure dolor minim veniam</div>
  <div class="abs pcap" style="left:339px;top:304px">Duis aute irure dolor minim veniam</div>
  <div class="abs link" style="left:413px;top:337px">View More +</div>
</section>

<section class="abs panel serv">
  <div class="abs tab" style="left:-4px;top:8px;width:154px">Our Services</div>
  <div class="abs svc" style="left:16px;background:linear-gradient(120deg,#d03050,#e8c040,#40a070,#3060c0)" role="img" aria-label="Colour swatches for prepress"><span>PREPRESS</span></div>
  <div class="abs svc" style="left:170px;background:linear-gradient(#8a5a3a,#c08a5a 50%,#6a4a3a)" role="img" aria-label="Warehouse shelving with stock"><span>INVENTORY MANAGEMENT</span></div>
  <div class="abs svc" style="left:324px;background:linear-gradient(#e8e8e8,#7a7a7a 60%,#2a2a3a)" role="img" aria-label="Business meeting around a table"><span>CONSULTING</span></div>
</section>

<section class="abs panel clients">
  <div class="abs tab" style="left:-4px;top:8px;width:154px">Our Clients</div>
  <div class="abs circ" style="left:13px"></div>
  <div class="abs cl" style="left:62px">Novaris</div>
  <div class="abs cl" style="left:189px;width:92px;background:#4a4a4a;color:#fff;text-align:center">Brightcore</div>
  <div class="abs cl" style="left:316px">Medalia</div>
  <div class="abs circ" style="left:446px"></div>
</section>

<footer class="abs">
  <h4 class="abs" style="left:98px;top:18px">About Us</h4>
  <p class="abs" style="left:98px;top:42px;width:193px">Printwell, Inc. is located in Alder Park, Georgia, just north of downtown Atlanta. Printwell's 45,000 sq. ft. facility is strategically located close to the transportation hub of the southeast which enables us to efficiently deliver your product anywhere around the globe.</p>
  <div class="abs link" style="left:98px;top:140px;color:#fff;font-size:9.5px">Read More &gt;&gt;</div>

  <h4 class="abs" style="left:355px;top:18px">Testimonials</h4>
  <div class="abs" style="left:354px;top:28px;font:900 28px/20px Georgia,serif;color:#2a8ae0">“</div>
  <div class="abs quote">iaculis dignissim sit amet sit amet lorem. Aenean rhoncus elit nec r sit get lorem. Aenean rhoncus elit nec r sit get porta.</div>
  <p class="abs" style="left:403px;top:122px"><b>Lorem,</b> lorem</p>
  <div class="abs" style="left:513px;top:118px;font:900 28px/20px Georgia,serif;color:#2a8ae0">”</div>
  <div class="abs link" style="left:358px;top:140px;color:#fff;font-size:9.5px">View All &gt;&gt;</div>

  <h4 class="abs" style="left:601px;top:18px">Contact Us</h4>
  <svg class="abs" style="left:603px;top:44px" width="16" height="22" viewBox="0 0 16 22"><path d="M8 0a7 7 0 0 0-7 7c0 5 7 15 7 15s7-10 7-15a7 7 0 0 0-7-7z" fill="#fff"/><circle cx="8" cy="7" r="2.6" fill="#174e86"/></svg>
  <p class="abs" style="left:626px;top:44px">120 Meadow Works Lane<br>Alder Park, GA 30000</p>
  <svg class="abs" style="left:602px;top:84px" width="18" height="12" viewBox="0 0 18 12"><rect x=".5" y=".5" width="17" height="11" fill="none" stroke="#fff"/><path d="M.5.5l8.5 6 8.5-6" stroke="#fff" fill="none"/></svg>
  <p class="abs" style="left:626px;top:83px">studio@printwell.example</p>
  <div class="abs" style="left:603px;top:106px;font:900 24px/28px Roboto,sans-serif;letter-spacing:1px">PRINTWELL</div>

  <div class="abs bar">
    <div style="position:absolute;left:95px;white-space:nowrap"><span>Home</span><span>Markets</span><span>Products</span><span>Services</span><span>About Us</span><span>Contact Us</span><span>Customer Service</span><span>FTP</span></div>
    <svg class="abs" style="left:548px;top:9px" width="18" height="18" viewBox="0 0 24 24"><path d="M6.6 10.8a15 15 0 0 0 6.6 6.6l2.2-2.2c.3-.3.7-.4 1-.2 1.1.4 2.3.6 3.6.6.6 0 1 .4 1 1V20c0 .6-.4 1-1 1A17 17 0 0 1 3 4c0-.6.4-1 1-1h3.5c.6 0 1 .4 1 1 0 1.3.2 2.5.6 3.6.1.3 0 .7-.2 1z" fill="#fff"/></svg>
    <div class="abs" style="left:573px;top:0;font:400 19px/36px Roboto,sans-serif">770.555.0186</div>
    <div class="abs" style="left:712px;top:-11px;width:60px;height:60px;border-radius:50%;background:radial-gradient(#f6d54a,#d9a515);border:3px dashed #f0c030" role="img" aria-label="Satisfaction guarantee seal"></div>
  </div>
  <p class="abs" style="left:95px;top:210px;font-size:9.5px">© 2014 Printwell. All rights reserved.</p>
  <div class="abs soc" style="left:600px;top:203px"></div>
  <div class="abs soc" style="left:630px;top:203px"></div>
  <div class="abs soc" style="left:660px;top:203px"></div>
</footer>
</body>
</html>
```